Global (re)insurance broker needs a business card design

We need a classic business card for our company that is headquartered in SG, with offices in Malaysia and Dubai. We specialise in insurance and reinsurance broking and consultancy for our global clients.

```html
<!DOCTYPE html>
<html lang="en">
<head>
<meta charset="utf-8">
<title>Korvale Business Card</title>
<link href="https://fonts.googleapis.com/css2?family=Open+Sans:wght@400;600;700&family=Montserrat:wght@500;600&display=swap" rel="stylesheet">
<style>
  :root {
    --page: #2a2a2e;
    --card-dark: #1f1f24;
    --mint: #c3e4bb;
    --mint-deep: #a9d4a0;
    --brand-blue: #2747a0;
    --ink-light: #f2f4f2;
    --emboss: #141417;
  }
  * { margin: 0; padding: 0; box-sizing: border-box; }
  html, body { width: 1200px; height: 780px; overflow: hidden; }
  body {
    background: var(--page);
    font-family: "Open Sans", sans-serif;
    display: flex;
    align-items: center;
    justify-content: center;
    gap: 40px;
  }
  .card {
    position: relative;
    width: 540px;
    height: 310px;
    border-radius: 22px;
    overflow: hidden;
  }
  /* Front */
  .card--front {
    background: var(--mint);
  }
  .card--front .pattern {
    position: absolute;
    inset: 0;
    background: linear-gradient(135deg, var(--mint-deep) 0%, var(--mint) 55%, #d3ecce 100%);
  }
  .card--front .front-name {
    position: absolute;
    right: 40px;
    bottom: 34px;
    font-family: "Montserrat", sans-serif;
    font-weight: 600;
    font-size: 16px;
    letter-spacing: 0.5px;
    color: #ffffff;
  }
  /* Back */
  .card--back {
    background: var(--card-dark);
    border: 2px solid var(--mint);
  }
  .accent-bar {
    position: absolute;
    top: 0;
    right: 26px;
    width: 12px;
    height: 60px;
    background: var(--mint);
  }
  .identity {
    position: absolute;
    top: 22px;
    right: 48px;
    text-align: left;
  }
  .identity .person-name {
    font-weight: 700;
    font-size: 30px;
    line-height: 1;
    color: var(--brand-blue);
  }
  .identity .person-name span { color: var(--mint); }
  .identity .person-role {
    font-size: 12.5px;
    color: var(--ink-light);
    margin-top: 4px;
  }
  .company-name {
    position: absolute;
    left: 30px;
    top: 100px;
    font-family: "Montserrat", sans-serif;
    font-weight: 600;
    font-size: 52px;
    letter-spacing: 1px;
    color: var(--mint);
  }
  .company-name--emboss {
    left: auto;
    top: auto;
    right: 18px;
    bottom: 30px;
    font-size: 58px;
    color: var(--emboss);
  }
  .contact {
    position: absolute;
    left: 30px;
    bottom: 22px;
    font-size: 12.5px;
    line-height: 1.45;
    color: var(--ink-light);
    list-style: none;
  }
  .contact .address { margin-bottom: 6px; }
  .contact li { display: flex; align-items: center; gap: 8px; }
  .contact .address { display: block; padding-left: 0; }
  .contact svg { width: 12px; height: 12px; flex: none; }
</style>
</head>
<body>
  <section class="card card--front" aria-label="Card front">
    <div class="pattern" role="img" aria-label="Repeating brand-name pattern in light green tones"></div>
    <div class="front-name">KORVALE</div>
  </section>

  <section class="card card--back" aria-label="Card back">
    <div class="accent-bar"></div>
    <div class="identity">
      <div class="person-name">Maren <span>Osei</span></div>
      <div class="person-role">Chief Operating Officer</div>
    </div>

    <div class="company-name">KORVALE</div>
    <div class="company-name company-name--emboss" aria-hidden="true">KORVALE</div>

    <ul class="contact">
      <li class="address">28 Harbour Lane, Meridian<br>Tower #08-04, Singapore 048500</li>
      <li>
        <svg viewBox="0 0 12 12"><rect x="3" y="1" width="6" height="10" rx="1.2" fill="none" stroke="#f2f4f2" stroke-width="1"/></svg>
        +65 9100 2345
      </li>
      <li>
        <svg viewBox="0 0 12 12"><circle cx="6" cy="6" r="5" fill="#2747a0"/><path d="M1 6h10M6 1c2 2 2 8 0 10M6 1c-2 2-2 8 0 10" stroke="#f2f4f2" stroke-width="0.7" fill="none"/></svg>
        www.korvale.com
      </li>
      <li>
        <svg viewBox="0 0 12 12"><rect x="1" y="3" width="10" height="7" fill="none" stroke="#f2f4f2" stroke-width="1"/><path d="M1 3l5 4 5-4" fill="none" stroke="#f2f4f2" stroke-width="1"/></svg>
        maren@korvale.com
      </li>
    </ul>
  </section>
</body>
</html>
```